Advertising company unique advertising platform

we need a logo design for a new company based in Australia Melbourne. We develop innovated advertising platform where consumer can use this platform to get regular discount, as business owner they can use this platform for free advertisement. Payment for this advertisement platform only payable every two weeks, when I generate revenue for their business

Industry/Entity Type

Advertising

Contact Information for Business Card

Dale Morven | Co-Founder |Managing Director
Suite 718 240 Wattlebrook Lane Melbourne Vic 3000

ABN 38 614 207 923
Tel: +61 0487 259 318 | Email: dale.morven@plivorantu.com

Font styles to use
Decorative
Script

Requirements
Must have
• Try few different design and some round corner business card
Should not have
• One round corner business card...try 4 different colour background not only black, make sure two side is designed. Be creative so imagine you are giving this to a client make sure has wow factor, if you can also try one design with engrave like all the logo, words look 3d feel
• The word Advertising Platform use attached file font

```html
<!DOCTYPE html>
<html lang="en">
<head>
<meta charset="utf-8">
<title>Kindlepath Business Card</title>
<link rel="stylesheet" href="https://fonts.googleapis.com/css2?family=Roboto:wght@400;500;700&display=swap">
<style>
  :root {
    --bg: #e9e6e2;
    --orange-hot: #e2452b;
    --orange-mid: #f07a2a;
    --yellow-glow: #f6c13c;
    --ink-dark: #1f1a17;
    --card-dark: #2a2a2b;
    --red-name: #ea4a2e;
    --teal: #2fd3b0;
    --blue: #3aa8e8;
    --text-light: #f2f2f2;
    --rule: #d8d8d8;
  }
  * { margin: 0; padding: 0; box-sizing: border-box; }
  html, body {
    width: 1200px; height: 886px; overflow: hidden;
    background: var(--bg);
    font-family: "Roboto", sans-serif;
  }
  .canvas { position: relative; width: 1200px; height: 886px; }

  .card {
    position: absolute;
    width: 520px; height: 318px;
    border-radius: 18px;
    overflow: hidden;
    box-shadow: 0 10px 28px rgba(0,0,0,.22);
  }

  /* Front side */
  .card-front {
    left: 70px; top: 110px;
    background: radial-gradient(ellipse at 45% 40%, var(--yellow-glow) 0%, var(--orange-mid) 45%, var(--orange-hot) 100%);
  }
  .front-brand {
    position: absolute; left: 0; right: 0; top: 110px;
    display: flex; justify-content: center; align-items: center; gap: 14px;
  }
  .brand-dot {
    width: 44px; height: 44px; border-radius: 50%;
    background: var(--ink-dark);
  }
  .front-brand .brand-name {
    font-size: 46px; font-weight: 700; color: var(--ink-dark);
    letter-spacing: 1px;
  }
  .front-web {
    position: absolute; left: 0; right: 0; bottom: 42px;
    text-align: center;
    font-size: 13px; letter-spacing: 5px; color: var(--ink-dark);
  }

  /* Back side */
  .card-back {
    left: 610px; top: 470px;
    background: var(--card-dark);
    color: var(--text-light);
  }
  .contact-block { position: absolute; left: 28px; top: 40px; width: 230px; }
  .person-name {
    font-size: 19px; font-weight: 500; color: var(--red-name);
    text-transform: uppercase; letter-spacing: .3px;
  }
  .person-role {
    font-size: 13px; font-weight: 500; color: var(--teal);
    text-transform: uppercase; line-height: 1.3; margin-top: 4px;
  }
  .contact-list { list-style: none; margin-top: 12px; font-size: 12.5px; line-height: 1.55; }
  .contact-list li { display: flex; align-items: center; gap: 8px; }
  .contact-list .icon { width: 11px; height: 11px; flex: none; }
  .contact-list .plain { padding-left: 0; }

  .divider {
    position: absolute; left: 28px; right: 28px; top: 130px;
    height: 1px; background: var(--rule);
  }
  .divider-short {
    position: absolute; left: 28px; width: 200px; top: 128px; height: 1px; background: var(--rule);
  }

  .back-brand {
    position: absolute; right: 32px; top: 50px;
    display: flex; align-items: center; gap: 12px;
  }
  .back-brand .brand-dot { background: var(--orange-mid); width: 36px; height: 36px; }
  .back-brand .brand-name {
    font-size: 36px; font-weight: 700; color: var(--orange-mid); letter-spacing: 1px;
  }

  .address {
    position: absolute; right: 30px; top: 200px;
    text-align: right; font-size: 14px; line-height: 1.45;
  }

  .bottom-band { position: absolute; left: 0; bottom: 0; width: 520px; height: 40px; }
  .band-web {
    position: absolute; right: 30px; bottom: 8px;
    font-size: 14px; letter-spacing: 2px; color: #fff6df;
  }
</style>
</head>
<body>
<div class="canvas">

  <section class="card card-front" aria-label="Card front">
    <div class="front-brand">
      <span class="brand-dot"></span>
      <span class="brand-name">Kindlepath</span>
    </div>
    <p class="front-web">www.plivorantu.com</p>
  </section>

  <section class="card card-back" aria-label="Card back">
    <div class="contact-block">
      <h1 class="person-name">Dale Morven</h1>
      <p class="person-role">Co-Founder<br>Managing Director</p>
      <ul class="contact-list">
        <li>
          <svg class="icon" viewBox="0 0 12 12"><path d="M2.5 1l2 2.5-1.2 1.2a7 7 0 0 0 4 4L8.5 7.5 11 9.5 9.8 11C5 11 1 7 1 2.2z" fill="var(--red-name)"/></svg>
          +61 0487 259 318
        </li>
        <li>
          <svg class="icon" viewBox="0 0 12 12"><rect x="0.5" y="2.5" width="11" height="7.5" fill="var(--red-name)"/><path d="M0.5 2.5L6 7l5.5-4.5" stroke="var(--card-dark)" stroke-width="1" fill="none"/></svg>
          dale.morven@plivorantu.com
        </li>
        <li class="plain">Plivorantu</li>
        <li class="plain">ABN 38 614 207 923</li>
      </ul>
    </div>

    <div class="back-brand">
      <span class="brand-dot"></span>
      <span class="brand-name">Kindlepath</span>
    </div>

    <div class="divider" style="top:168px; left:230px;"></div>
    <div class="divider-short" style="top:108px;"></div>

    <p class="address">Suite 718 240 Wattlebrook Lane<br>Melbourne Vic 3000</p>

    <svg class="bottom-band" viewBox="0 0 520 40" preserveAspectRatio="none" aria-hidden="true">
      <defs>
        <linearGradient id="bandFill" x1="0" x2="1" y1="0" y2="0">
          <stop offset="0" stop-color="var(--orange-hot)"/>
          <stop offset="0.45" stop-color="var(--yellow-glow)"/>
          <stop offset="1" stop-color="var(--orange-hot)"/>
        </linearGradient>
        <linearGradient id="stripeFill" x1="0" x2="1" y1="0" y2="0">
          <stop offset="0" stop-color="var(--teal)"/>
          <stop offset="0.5" stop-color="var(--yellow-glow)"/>
          <stop offset="1" stop-color="var(--blue)"/>
        </linearGradient>
      </defs>
      <path d="M0 22 L236 22 L236 26 L0 26 Z" fill="url(#stripeFill)"/>
      <path d="M0 28 L230 28 Q238 28 244 20 L250 12 Q254 8 262 8 L520 8 L520 40 L0 40 Z" fill="url(#bandFill)"/>
    </svg>
    <p class="band-web">www.plivorantu.com</p>
  </section>

</div>
</body>
</html>
```